Business Card Design

Hi I need a business card designed, we already have the business name logo artwork and would like some concept ideas for the Bus Card layout.
On the back of the card i want to include the products and services that we offer.
We are a Plastics Sheeting manufacture based in Perth Australia.

                                       

We need a BC design for a company called Tarvo Plastics based in Perth Australia.

We supply from DIY to Trade & Industrial  Engineering Markets.

We specialise in:

·         Cut to size panels  (all shapes and sizes)

·         Plastics fabrication & Welding

·         Custom Designs

·         Plastic Repairs

·         PVC Pipe Slotting & PVC Pipe Threading

·         Supplier of all types of engineering plastics and profiles.

Including:           Acrylic / Clarvene

                               Polycarbonate / Dorvil

                               Prismatic Light Diffuser

                               Vantrib

                               HDPE / UHMWPE

                               PVC / PVC Foam

                               Nylon

                               HIPS

```html
<!DOCTYPE html>
<html lang="en">
<head>
<meta charset="utf-8">
<title>Tarvo Plastics – Business Card</title>
<link rel="stylesheet" href="https://fonts.googleapis.com/css2?family=Open+Sans:ital,wght@0,400;0,600;0,700;0,800;1,700&display=swap">
<style>
  :root {
    --navy: #0d2a5e;
    --green: #4a9138;
    --white: #ffffff;
    --ink: #333333;
    --orange: #e5781e;
    --yellow: #e8a817;
    --red: #c8202b;
    --stage: #e9e9ee;
    --divider: rgba(255,255,255,0.55);
  }
  * { box-sizing: border-box; margin: 0; padding: 0; }
  html, body { width: 1200px; height: 987px; overflow: hidden; }
  body {
    background: var(--stage);
    font-family: "Open Sans", sans-serif;
    position: relative;
  }
  .card {
    position: absolute;
    left: 240px;
    width: 720px;
    height: 440px;
    border-radius: 30px;
    overflow: hidden;
    box-shadow: 0 6px 18px rgba(0,0,0,0.12);
  }
  .card-front { top: 24px; background: var(--white); }
  .card-back { top: 520px; background: var(--green); }

  /* front */
  .front-swoosh { position: absolute; inset: 0; }
  .brand {
    position: absolute;
    display: flex;
    align-items: center;
    gap: 14px;
    font-weight: 800;
    color: var(--navy);
    white-space: nowrap;
  }
  .brand-mark { background: var(--red); flex: none; }
  .brand-front { top: 52px; left: 150px; font-size: 66px; line-height: 1; }
  .brand-front .brand-mark { width: 30px; height: 30px; }
  .contacts {
    position: absolute;
    top: 160px;
    left: 210px;
    color: var(--ink);
    font-size: 19px;
    line-height: 1.45;
  }
  .contact-row { display: flex; gap: 22px; }
  .contact-item { display: flex; align-items: center; gap: 7px; }
  .contact-item svg { width: 18px; height: 18px; fill: var(--navy); }
  .legal { font-size: 15px; margin-top: 4px; }
  .address { font-size: 19px; }
  .person {
    position: absolute;
    right: 46px;
    bottom: 28px;
    text-align: right;
    color: var(--white);
  }
  .person-name { font-size: 30px; font-weight: 700; line-height: 1.1; }
  .person-title { font-size: 20px; }

  /* back */
  .brand-back { top: 26px; right: 40px; font-size: 50px; line-height: 1; }
  .brand-back .brand-mark { width: 24px; height: 24px; }
  .tagline {
    position: absolute;
    top: 98px;
    left: 40px;
    right: 40px;
    text-align: center;
    color: var(--navy);
    font-weight: 700;
    font-style: italic;
    font-size: 17px;
    line-height: 1.3;
  }
  .col {
    position: absolute;
    top: 162px;
    color: var(--white);
  }
  .col-services { left: 36px; width: 330px; }
  .col-materials { left: 410px; width: 290px; }
  .col-heading { font-size: 21px; font-weight: 700; margin-bottom: 4px; }
  .col-materials .col-heading { color: var(--navy); font-weight: 800; }
  .col ul { list-style: none; font-size: 16px; line-height: 1.4; }
  .col li { padding-left: 14px; position: relative; }
  .col li::before { content: "•"; position: absolute; left: 0; }
  .col-divider {
    position: absolute;
    left: 385px;
    top: 170px;
    width: 1px;
    height: 230px;
    background: var(--divider);
  }
  .pair-row { display: flex; gap: 22px; }
</style>
</head>
<body>

<section class="card card-front" aria-label="Front of business card">
  <svg class="front-swoosh" viewBox="0 0 720 440" width="720" height="440" aria-hidden="true">
    <path d="M0,150 C20,300 200,352 400,342 C540,335 650,312 720,292 L720,440 L0,440 Z" fill="var(--navy)"/>
    <path d="M0,148 C20,300 200,350 400,340 C540,333 650,310 720,290" fill="none" stroke="var(--white)" stroke-width="3"/>
    <path d="M0,150 C8,210 30,250 60,282" fill="none" stroke="var(--orange)" stroke-width="6"/>
    <path d="M440,328 C560,318 650,298 720,278" fill="none" stroke="var(--yellow)" stroke-width="7"/>
  </svg>

  <div class="brand brand-front"><span class="brand-mark"></span>Tarvo Plastics</div>

  <div class="contacts">
    <div class="contact-row">
      <span class="contact-item">
        <svg viewBox="0 0 24 24"><path d="M6.6 10.8a15 15 0 0 0 6.6 6.6l2.2-2.2a1 1 0 0 1 1-.25 11.4 11.4 0 0 0 3.6.57 1 1 0 0 1 1 1V20a1 1 0 0 1-1 1A17 17 0 0 1 3 4a1 1 0 0 1 1-1h3.5a1 1 0 0 1 1 1c0 1.25.2 2.45.57 3.57a1 1 0 0 1-.25 1z"/></svg>
        08 9000 4411
      </span>
      <span class="contact-item">
        <svg viewBox="0 0 24 24"><path d="M8 1h8a2 2 0 0 1 2 2v18a2 2 0 0 1-2 2H8a2 2 0 0 1-2-2V3a2 2 0 0 1 2-2zm0 3v14h8V4zm4 15.5a1 1 0 1 0 0 2 1 1 0 0 0 0-2z"/></svg>
        0400 555 019
      </span>
    </div>
    <div class="contact-row">
      <span class="contact-item">
        <svg viewBox="0 0 24 24"><path d="M6 2h9l3 3v5h1a3 3 0 0 1 3 3v7a2 2 0 0 1-2 2H4a2 2 0 0 1-2-2v-7a3 3 0 0 1 3-3h1zm2 2v6h8V6h-2V4zm-1 11v2h4v-2zm8 0v2h2v-2z"/></svg>
        08 9000 4422
      </span>
      <span class="contact-item">
        <svg viewBox="0 0 24 24"><path d="M3 5h18a1 1 0 0 1 1 1v12a1 1 0 0 1-1 1H3a1 1 0 0 1-1-1V6a1 1 0 0 1 1-1zm1 2.3V17h16V7.3l-8 5.2z"/></svg>
        sales@tarvoplastics.example
      </span>
    </div>
    <p class="legal">Korbell Holdings Pty Ltd T/A Tarvo Plastics ABN: TBA</p>
    <p class="address">Unit 4/18 Ferrow Circuit Lindale WA 6150</p>
    <p class="address">PO Box 2207 Lindale DC WA 6971</p>
  </div>

  <div class="person">
    <p class="person-name">Your Name</p>
    <p class="person-title">Title</p>
  </div>
</section>

<section class="card card-back" aria-label="Back of business card">
  <div class="brand brand-back"><span class="brand-mark"></span>Tarvo Plastics</div>
  <p class="tagline">The Products And Services That We Offer<br>Are Supplied From Diy To Trade &amp; Industrial Engineering Markets</p>

  <div class="col col-services">
    <h2 class="col-heading">We specialise in:</h2>
    <ul>
      <li>Cut to size panels (all shapes and sizes)</li>
      <li>Plastics fabrication &amp; Welding</li>
      <li>Custom Designs</li>
      <li>Plastic Repairs</li>
      <li>PVC Pipe Slotting &amp; PVC Pipe Threading</li>
      <li>Supplier of all types of engineering plastics and profiles</li>
    </ul>
  </div>

  <div class="col-divider"></div>

  <div class="col col-materials">
    <h2 class="col-heading">Including:</h2>
    <ul>
      <li>Acrylic / Clarvene</li>
      <li>Polycarbonate / Dorvil</li>
      <li>Prismatic Light Diffuser</li>
    </ul>
    <div class="pair-row"><ul><li>Vantrib</li></ul><ul><li>HDPE / UHMWPE</li></ul></div>
    <ul><li>PVC / PVC Foam</li></ul>
    <div class="pair-row"><ul><li>Nylon</li></ul><ul><li>HIPS</li></ul></div>
  </div>
</section>

</body>
</html>
```